Road Construction Company needs business cards

We would like a new business card designed for our business.

We're a road construction company based in Qld, Australia.

Can the business card please have the following information on it.

Name: Warren Halbeck
Position: General Manager
Phone: 0472 915 348
Email: Warren.halbeck@tovrin.com.au
Address: 87 Marrow Ave, Pendlebay, QLD, 4023
Website: www.tovrin.com.au

Visually we'd like the card to be professional and simple.

Attached is our logo.

Our website is www.tovrin.com.au

Target Market(s)

Men aged 25-60

Contact Information for Business Card

As listed in project description

Font styles to use
Serif

Requirements
Must have
• Large logo on back of card

```html
<!DOCTYPE html>
<html lang="en">
<head>
<meta charset="utf-8">
<title>Tovrin Business Card</title>
<link rel="stylesheet" href="https://fonts.googleapis.com/css2?family=Figtree:wght@400;700;800&display=swap">
<style>
  :root {
    --backdrop: #e3e3e3;
    --brand-blue: #0b4da2;
    --brand-blue-light: #1466ad;
    --ink-navy: #0c3f8f;
    --ink-grey: #555a60;
    --rule-blue: #2b95cf;
    --card-white: #f2f2f2;
    --paper-white: #f4f2ef;
  }
  * { margin: 0; padding: 0; box-sizing: border-box; }
  html, body {
    width: 1200px; height: 1200px; overflow: hidden;
    background: var(--backdrop);
    font-family: "Figtree", Arial, sans-serif;
  }
  .canvas { position: relative; width: 1200px; height: 1200px; }
  .card {
    position: absolute; left: 234px; width: 730px; height: 418px;
  }
  .card--front {
    top: 160px;
    background: linear-gradient(115deg, #084694 0%, var(--brand-blue) 45%, var(--brand-blue-light) 100%);
  }
  .card--back {
    top: 632px;
    background: linear-gradient(115deg, #ebebeb 0%, var(--card-white) 60%, #f7f7f7 100%);
  }
  .front-wordmark {
    position: absolute; left: 0; right: 0; top: 148px;
    text-align: center;
    font-weight: 800; font-size: 92px; letter-spacing: 4px; line-height: 1;
    color: var(--paper-white);
  }
  .holder-name {
    position: absolute; left: 64px; top: 60px;
    font-weight: 700; font-size: 31px; color: var(--ink-navy); line-height: 1;
  }
  .holder-role {
    position: absolute; left: 65px; top: 100px;
    font-size: 19px; color: var(--ink-grey); line-height: 1;
  }
  .divider {
    position: absolute; left: 64px; top: 140px; width: 596px; height: 2px;
    background: var(--rule-blue);
  }
  .address {
    position: absolute; left: 64px; top: 208px;
    font-size: 19px; line-height: 26px; color: var(--ink-grey);
  }
  .contact-list {
    position: absolute; left: 64px; top: 272px; list-style: none;
  }
  .contact-list li {
    display: flex; align-items: center; height: 28px;
    font-size: 19px; color: var(--ink-grey);
  }
  .contact-list svg { width: 16px; height: 16px; margin-right: 10px; fill: var(--ink-navy); flex: none; }
  .back-wordmark {
    position: absolute; left: 421px; width: 237px; top: 306px;
    text-align: center;
    font-weight: 800; font-size: 40px; letter-spacing: 2px; line-height: 1;
    color: var(--ink-navy);
  }
</style>
</head>
<body>
<main class="canvas">
  <section class="card card--front">
    <div class="front-wordmark">TOVRIN</div>
  </section>

  <section class="card card--back">
    <h1 class="holder-name">Warren Halbeck</h1>
    <p class="holder-role">General Manager</p>
    <div class="divider"></div>
    <p class="address">87 Marrow Ave, Pendlebay,<br>QLD, 4023</p>
    <ul class="contact-list">
      <li>
        <svg viewBox="0 0 16 16" aria-hidden="true"><path d="M3.2 1.5l2.3 2.3-1.3 1.8c.9 2 2.4 3.5 4.3 4.4l1.8-1.3 2.3 2.3-1.6 2.2C6.4 13 3 9.6 1 4.8z"/><path d="M9 1.5a5.5 5.5 0 0 1 5.5 5.5h-1.3A4.2 4.2 0 0 0 9 2.8zM9 4a3 3 0 0 1 3 3h-1.3A1.7 1.7 0 0 0 9 5.3z"/></svg>
        0472 915 348
      </li>
      <li>
        <svg viewBox="0 0 16 16" aria-hidden="true"><path d="M1 3h14v10H1z M2.2 4.2v.4L8 8.8l5.8-4.2v-.4z" fill-rule="evenodd"/></svg>
        Warren.halbeck@tovrin.com.au
      </li>
      <li>
        <svg viewBox="0 0 16 16" aria-hidden="true"><path d="M8 1a7 7 0 1 0 0 14A7 7 0 0 0 8 1zm-1 1.6V7H3.3A5 5 0 0 1 7 2.6zm2 0A5 5 0 0 1 12.7 7H9zM3.3 9H7v4.4A5 5 0 0 1 3.3 9zM9 9h3.7A5 5 0 0 1 9 13.4z"/></svg>
        www.tovrin.com.au
      </li>
    </ul>
    <div class="back-wordmark">TOVRIN</div>
  </section>
</main>
</body>
</html>
```